cryotherapy business . Whole Body Cryotherapy, Localised Cryotherapy, Cryofacials

Need home page plus services, about, pricing, online booking, contact and blog page

I want something slick, hip and professional. Our studio colours are duck egg blue, white and grey

I would also like a social media scroll at the bottom of every page

I will upload some web designs that I like the look of

Target Market(s)

Men and Women 25-45

Industry/Entity Type

Health And Wellness

Coding

Coded - Design and coding required

Number of Pages Required

5+ page

Font styles to use
Serif
Sans Serif

Requirements
Must have
• Must be eye catching and easy to navigate
Nice to have
• animation
Should not have
• Not sure what the site should not have. I am fairly open to ideas as this is a brand new business.

```html
<!DOCTYPE html>
<html lang="en">
<head>
<meta charset="utf-8">
<title>Frost Haven – Cryotherapy Studio</title>
<link href="https://fonts.googleapis.com/css2?family=Lato:wght@400;700&family=Raleway:wght@400;500;600&family=Roboto:wght@500;700&display=swap" rel="stylesheet">
<style>
:root{
  --duck-egg:#a9cdd6;
  --duck-egg-deep:#8fbcc7;
  --mint:#9ed6c9;
  --ink:#111111;
  --charcoal:#333333;
  --grey-text:#666666;
  --light-grey:#ececec;
  --ghost:#e6e6e6;
  --hero-deep:#1c4fb0;
  --hero-mid:#3f74d0;
  --hero-light:#7ea6e2;
  --white:#ffffff;
  --faq-green:#3aa56b;
}
*{box-sizing:border-box;margin:0;padding:0}
html,body{width:1200px;height:5159px;overflow:hidden}
body{position:relative;font-family:"Lato",sans-serif;color:var(--charcoal);background:var(--white)}
.abs{position:absolute}
section,header,footer{position:absolute;left:0;width:1200px}

/* top bar */
.topbar{top:0;height:66px;background:var(--ink)}
.social-mini{top:24px;width:20px;height:20px;border-radius:3px;background:var(--white)}
.phone{left:602px;top:13px;display:flex;align-items:center;gap:12px;color:var(--white);font-family:"Raleway",sans-serif;font-size:22px;font-weight:500}
.phone-icon{width:40px;height:40px;border:2px solid var(--white);border-radius:50%;display:flex;align-items:center;justify-content:center}
.search{left:854px;top:16px;width:232px;height:36px;border-radius:18px;background:var(--white);padding:0 18px;display:flex;align-items:center;justify-content:space-between;font-size:15px;color:#777}

/* hero */
.hero{top:66px;height:600px;background:radial-gradient(ellipse at 30% 30%,var(--hero-light),transparent 55%),radial-gradient(ellipse at 75% 60%,var(--hero-mid),transparent 60%),linear-gradient(160deg,var(--hero-mid),var(--hero-deep) 60%,#2a5ec2)}
.logo{font-family:"Raleway",sans-serif;font-weight:500;color:var(--white);font-size:30px;letter-spacing:1px}
.hero .logo{left:120px;top:34px}
.nav{left:414px;top:44px;display:flex;gap:30px;font-family:"Raleway",sans-serif;font-size:14.5px;color:var(--white);text-transform:uppercase}
.hero-welcome{left:0;width:1200px;top:200px;text-align:center;font-family:"Raleway",sans-serif;font-weight:500;font-size:62px;color:var(--white)}
.hero-name{left:0;width:1200px;top:272px;text-align:center;font-family:"Raleway",sans-serif;font-weight:400;font-size:78px;letter-spacing:14px;color:var(--white)}
.hero-arrow{top:280px;width:46px;height:46px;border:3px solid var(--white);border-radius:50%}
.enquire{left:526px;top:444px;width:154px;height:38px;border:1px solid var(--white);color:var(--white);font-family:"Raleway",sans-serif;font-size:14px;display:flex;align-items:center;justify-content:center}

/* shared headings */
.ghost{font-family:"Roboto",sans-serif;font-weight:700;color:var(--ghost);font-size:66px;letter-spacing:1px;white-space:nowrap}
.title{font-family:"Roboto",sans-serif;font-weight:700;font-size:38px;color:var(--charcoal);white-space:nowrap}
.rule{height:4px;width:66px;background:var(--duck-egg)}
.deco-line{height:3px;background:var(--ink)}
.deco-dot{width:20px;height:20px;border-radius:50%;background:var(--mint)}

/* about */
.about{top:666px;height:600px}
.about-photo{left:100px;top:64px;width:400px;height:430px;border-radius:8px;background:linear-gradient(120deg,#e9eef4,#c7d4ea 40%,#2f54a8 55%,#e6e8ec 80%,#ffffff)}
.about p{left:516px;top:304px;width:574px;font-size:13.6px;line-height:27.5px;color:var(--charcoal);text-align:justify}
.btn-pale{background:var(--duck-egg);color:var(--charcoal);font-size:16px;display:flex;align-items:center;justify-content:center}

/* expect */
.expect{top:1266px;height:708px;background:linear-gradient(90deg,#15254a 0%,#0c0c10 22%,#000 45%,#000 100%)}
.expect-glow{left:0;top:0;width:330px;height:400px;background:radial-gradient(ellipse at 20% 30%,#3e62b0,transparent 65%)}
.expect .title{color:var(--white)}
.expect .ghost{color:#1e1e1e}
.expect-intro{left:0;width:1200px;top:186px;text-align:center;color:var(--white);font-size:13.5px;line-height:26px}
.step{top:276px;width:312px;height:352px}
.step-photo{left:0;top:0;width:312px;height:196px;background:linear-gradient(135deg,#d9dde3,#a7b0bd 50%,#eef0f2)}
.step-card{left:16px;top:188px;width:280px;height:160px;background:#fffdf4;text-align:center}
.step-label{left:76px;top:-12px;width:128px;height:30px;background:var(--duck-egg);font-family:"Roboto",sans-serif;font-weight:500;font-size:16px;color:var(--ink);display:flex;align-items:center;justify-content:center}
.step-text{left:14px;top:26px;width:252px;font-size:13px;line-height:22px;color:#555}
.step-more{left:0;width:280px;top:112px;font-size:17px;color:var(--charcoal);font-weight:700}

/* pricing */
.pricing{top:1974px;height:702px;background:var(--light-grey)}
.pricing .ghost{color:#d9d9d9}
.plan{top:216px;width:316px;height:414px;background:var(--duck-egg);border:2px solid #c3d9df;text-align:center}
.plan-head{left:0;width:312px;top:14px;font-family:"Roboto",sans-serif;font-weight:700;font-size:26px;color:var(--ink)}
.plan-photo{left:2px;top:68px;width:308px;height:190px}
.plan-name{left:0;width:312px;top:266px;font-size:20px;color:var(--ink)}
.plan-price{left:0;width:312px;top:298px;font-family:"Raleway",sans-serif;font-weight:600;font-size:34px;color:var(--ink)}
.buy{left:94px;top:352px;width:124px;height:46px;background:var(--ink);color:var(--white);font-family:"Roboto",sans-serif;font-weight:700;font-size:19px;display:flex;align-items:center;justify-content:center}

/* faq */
.faq{top:2676px;height:774px}
.faq-item{left:110px;width:950px;border:2px solid #cfd8dc;background:var(--white)}
.faq-q{position:absolute;left:54px;top:13px;font-size:19px;color:var(--charcoal)}
.faq-open .faq-q{color:var(--faq-green)}
.faq-a{position:absolute;left:54px;top:60px;width:780px;font-size:13px;line-height:28px;color:#555}
.caret{position:absolute;right:36px;top:24px}

/* testimonial */
.testimonial{top:3450px;height:540px;background:radial-gradient(ellipse at 30% 70%,#2b3038,transparent 60%),linear-gradient(180deg,#14171c,#1f242b)}
.quote-card{left:184px;top:80px;width:830px;height:372px;background:var(--white)}
.avatar{left:386px;top:32px;width:98px;height:98px;transform:rotate(45deg);border:2px solid var(--duck-egg);background:linear-gradient(135deg,#dcdcdc,#6d6d6d)}
.quote-text{left:100px;width:630px;top:196px;text-align:center;font-size:13px;line-height:27px;color:#555}
.dots{left:382px;top:304px;display:flex;gap:10px;align-items:center}
.dots span{width:11px;height:11px;background:var(--duck-egg);transform:rotate(45deg)}
.dots span.on{width:14px;height:14px;background:#84b6c3}

/* blog */
.blog{top:3990px;height:760px}
.post{top:244px;width:316px;height:392px;background:var(--white);box-shadow:0 2px 6px rgba(0,0,0,.15)}
.post-photo{left:0;top:0;width:316px;height:208px;background:linear-gradient(160deg,#5b6f86,#c9ced6 55%,#3b4450)}
.post-title{left:26px;top:232px;font-family:"Raleway",sans-serif;font-weight:500;font-size:20px;color:var(--charcoal)}
.post-text{left:26px;top:270px;width:264px;font-size:12.5px;line-height:18px;color:#666}
.post-meta{left:26px;top:358px;width:264px;display:flex;justify-content:space-between;font-size:11.5px;color:#777}
.post-meta span{display:flex;align-items:center;gap:8px}

/* footer */
.footer{top:4750px;height:409px;background:var(--duck-egg)}
.footer .logo{left:122px;top:126px;color:var(--ink);font-size:32px;font-weight:600}
.foot-about{left:120px;top:178px;width:220px;font-size:11.5px;line-height:22px;color:var(--charcoal);text-align:center}
.foot-head{font-family:"Raleway",sans-serif;font-weight:600;font-size:17px;color:var(--charcoal)}
.contact-line{display:flex;gap:12px;align-items:flex-start;font-size:13px;color:var(--charcoal);line-height:22px}
.nl-input{left:774px;top:164px;width:210px;height:42px;border:1px solid var(--white);font-size:12.5px;color:var(--charcoal);padding:13px 20px}
.nl-btn{left:984px;top:164px;width:106px;height:42px;background:var(--ink);color:var(--white);font-size:11.5px;font-weight:700;display:flex;align-items:center;justify-content:center}
.ring{top:248px;width:26px;height:26px;border:2px solid var(--ink);border-radius:50%}
.foot-rule{left:90px;top:328px;width:1000px;height:1px;background:#7fa7b2}
.copyright{left:122px;top:360px;font-size:13px;color:#4d6f78}
</style>
</head>
<body>

<header class="topbar">
  <div class="abs social-mini" style="left:120px"></div>
  <div class="abs social-mini" style="left:176px"></div>
  <div class="abs social-mini" style="left:232px"></div>
  <div class="abs phone">
    <div class="phone-icon"><svg width="20" height="20" viewBox="0 0 24 24"><path d="M6.6 10.8a15 15 0 0 0 6.6 6.6l2.2-2.2c.3-.3.7-.4 1-.2 1.1.4 2.3.6 3.6.6.6 0 1 .4 1 1V20c0 .6-.4 1-1 1A17 17 0 0 1 3 4c0-.6.4-1 1-1h3.5c.6 0 1 .4 1 1 0 1.3.2 2.5.6 3.6.1.3 0 .7-.2 1z" fill="#fff"/></svg></div>
    555-014-2290
  </div>
  <div class="abs search">Search<svg width="12" height="12" viewBox="0 0 12 12"><circle cx="5" cy="5" r="3.5" fill="none" stroke="#555" stroke-width="1.5"/><path d="M7.6 7.6 11 11" stroke="#555" stroke-width="1.5"/></svg></div>
</header>

<section class="hero" role="img" aria-label="Blue watercolour frost texture backdrop">
  <div class="abs logo">Frost Haven</div>
  <nav class="abs nav"><span>Home</span><span>Services</span><span>About</span><span>Pricing</span><span>Online</span><span>Booking</span><span>Contact &amp; Blog</span></nav>
  <div class="abs hero-welcome">Welcome to</div>
  <div class="abs hero-name">Frost Haven</div>
  <div class="abs hero-arrow" style="left:116px"><svg width="40" height="40" viewBox="0 0 40 40"><path d="M24 12 14 20l10 8M14 20h14" fill="none" stroke="#fff" stroke-width="3"/></svg></div>
  <div class="abs hero-arrow" style="left:1032px"><svg width="40" height="40" viewBox="0 0 40 40"><path d="M16 12l10 8-10 8M26 20H12" fill="none" stroke="#fff" stroke-width="3"/></svg></div>
  <div class="abs enquire">ENQUIRE NOW</div>
  <svg class="abs" style="left:596px;top:480px" width="14" height="10"><path d="M0 0h14L7 10z" fill="#fff"/></svg>
  <svg class="abs" style="left:0;top:560px" width="1200" height="40" viewBox="0 0 1200 40"><path d="M0 30 L40 22 L80 30 L130 18 L180 28 L240 20 L300 30 L360 22 L420 32 L480 20 L540 28 L600 18 L660 30 L720 22 L780 30 L840 20 L900 28 L960 18 L1020 30 L1080 22 L1140 14 L1200 8 V40 H0Z" fill="#fff"/></svg>
</section>

<section class="about">
  <div class="abs about-photo" role="img" aria-label="Cryotherapy cabin with a woman inside"></div>
  <div class="abs deco-line" style="left:770px;top:107px;width:430px"></div>
  <div class="abs deco-dot" style="left:752px;top:98px"></div>
  <div class="abs ghost" style="left:556px;top:158px">CRYOTHERAPY?</div>
  <h2 class="abs title" style="left:510px;top:196px">WHAT IS CRYOTHERAPY?</h2>
  <div class="abs rule" style="left:510px;top:262px"></div>
  <p class="abs">Originally invented by doctors as a powerful anti-inflammatory tool, cryotherapy is a quick, noninvasive process that exposes your body to extreme cold of up to -250°F. This sudden drop in temperature increases circulation and pumps reoxygenated and nutrient enriched blood back into the bloodstream reducing pain &amp; inflammation and alleviating sore muscles. It's also known to release 'feel good' endorphins that help improve sleep, reduce stress, and increase your metabolism.</p>
  <div class="abs btn-pale" style="left:522px;top:484px;width:114px;height:42px">Read More</div>
</section>

<section class="expect">
  <div class="abs expect-glow" role="img" aria-label="Woman inside a glowing cryo cabin"></div>
  <div class="abs ghost" style="left:466px;top:62px">EXPECT</div>
  <h2 class="abs title" style="left:0;width:1200px;text-align:center;top:100px">WHAT TO EXPECT</h2>
  <div class="abs rule" style="left:434px;top:162px"></div>
  <div class="abs expect-intro">As a first time client, we'll ask you for some information about your medical history and what your goals are.<br>Then once you've signed the waiver, you'll be ready to start.</div>

  <div class="abs step" style="left:108px">
    <div class="abs step-photo" role="img" aria-label="Client in a robe and mittens before a session"></div>
    <div class="abs step-card">
      <div class="abs step-label">BEFORE</div>
      <div class="abs step-text">Change into a robe/wrap (no jewelry or metal is allowed in the CryoCabin). Socks, slippers &amp; mittens are provid-</div>
      <div class="abs step-more">Read More</div>
    </div>
  </div>
  <div class="abs step" style="left:440px">
    <div class="abs step-photo" role="img" aria-label="Client inside the cabin during a session"></div>
    <div class="abs step-card">
      <div class="abs step-label">DURING</div>
      <div class="abs step-text">Change into a robe/wrap (no jewelry or metal is allowed in the CryoCabin). Socks, slippers &amp; mittens are provid-</div>
      <div class="abs step-more">Read More</div>
    </div>
  </div>
  <div class="abs step" style="left:774px">
    <div class="abs step-photo" role="img" aria-label="Client leaving the cabin after a session"></div>
    <div class="abs step-card">
      <div class="abs step-label">AFTER</div>
      <div class="abs step-text">Change into a robe/wrap (no jewelry or metal is allowed in the CryoCabin). Socks, slippers &amp; mittens are provid-</div>
      <div class="abs step-more">Read More</div>
    </div>
  </div>
</section>

<section class="pricing">
  <div class="abs deco-line" style="left:910px;top:102px;width:290px"></div>
  <div class="abs deco-dot" style="left:892px;top:93px"></div>
  <div class="abs ghost" style="left:576px;top:50px">PRICING</div>
  <h2 class="abs title" style="left:680px;top:88px">PRICING</h2>
  <div class="abs rule" style="left:730px;top:148px"></div>

  <div class="abs plan" style="left:90px">
    <div class="abs plan-head">MONTHLY*</div>
    <svg class="abs plan-photo" viewBox="0 0 308 190" role="img" aria-label="Woman wrapped in a towel beside a cabin"><defs><linearGradient id="p1" x1="0" y1="0" x2="1" y2="1"><stop offset="0" stop-color="#e5e2de"/><stop offset=".5" stop-color="#b9b2aa"/><stop offset="1" stop-color="#4a5668"/></linearGradient></defs><path d="M0 0H308V170Q154 200 0 170Z" fill="url(#p1)"/></svg>
    <div class="abs plan-name">Whole Body Cryotherapy</div>
    <div class="abs plan-price">$40</div>
    <div class="abs buy">Buy Now</div>
  </div>
  <div class="abs plan" style="left:440px">
    <div class="abs plan-head">MONTHLY*</div>
    <svg class="abs plan-photo" viewBox="0 0 308 190" role="img" aria-label="Woman receiving a cryo facial"><defs><linearGradient id="p2" x1="0" y1="0" x2="1" y2="1"><stop offset="0" stop-color="#cbb9a0"/><stop offset=".5" stop-color="#e9e4dc"/><stop offset="1" stop-color="#f4f4f4"/></linearGradient></defs><path d="M0 0H308V170Q154 200 0 170Z" fill="url(#p2)"/></svg>
    <div class="abs plan-name">Cryo Facial</div>
    <div class="abs plan-price">$720</div>
    <div class="abs buy">Buy Now</div>
  </div>
  <div class="abs plan" style="left:792px">
    <div class="abs plan-head">MONTHLY*</div>
    <svg class="abs plan-photo" viewBox="0 0 308 190" role="img" aria-label="Woman next to a cabin control display"><defs><linearGradient id="p3" x1="0" y1="0" x2="1" y2="1"><stop offset="0" stop-color="#9aa2ad"/><stop offset=".5" stop-color="#d8c9b5"/><stop offset="1" stop-color="#5a6270"/></linearGradient></defs><path d="M0 0H308V170Q154 200 0 170Z" fill="url(#p3)"/></svg>
    <div class="abs plan-name">Local Cryotherapy</div>
    <div class="abs plan-price">$400</div>
    <div class="abs buy">Buy Now</div>
  </div>
</section>

<section class="faq">
  <div class="abs deco-line" style="left:0;top:113px;width:272px"></div>
  <div class="abs deco-dot" style="left:270px;top:104px"></div>
  <div class="abs ghost" style="left:130px;top:150px">FAQ</div>
  <h2 class="abs title" style="left:110px;top:190px">FREQUENTLY ASKED QUESTIONS</h2>
  <div class="abs rule" style="left:110px;top:256px"></div>

  <div class="abs faq-item" style="top:308px;height:58px"><span class="faq-q">What is Cryotherapy?</span><svg class="caret" width="18" height="10"><path d="M0 10 9 0l9 10z" fill="#7fb3c2"/></svg></div>
  <div class="abs faq-item" style="top:378px;height:58px"><span class="faq-q">Why should I do Cryotherapy?</span></div>
  <div class="abs faq-item faq-open" style="top:450px;height:158px"><span class="faq-q">What is Cryotherapy?</span><svg class="caret" width="18" height="10"><path d="M0 0h18L9 10z" fill="#7fb3c2"/></svg>
    <p class="faq-a">Cryotherapy has a host of benefits. If you are either i) suffering from an injury or recovering from a surgical procedure ii) an athlete looking to enhance performance and alleviate sore muscles or iii) looking for ways to improve your general health &amp; wellness through improved sleep, reduced stress, and increased metabolism, Cryotherapy could be beneficial for you.</p></div>
  <div class="abs faq-item" style="top:630px;height:58px"><span class="faq-q">What is the difference between local Cryotherapy and ice packs?</span><svg class="caret" width="18" height="10"><path d="M0 10 9 0l9 10z" fill="#7fb3c2"/></svg></div>
</section>

<section class="testimonial" role="img" aria-label="Dim photo of clients in the studio">
  <div class="abs quote-card">
    <svg class="abs" style="left:60px;top:64px" width="62" height="50" viewBox="0 0 62 50"><path d="M0 50V28C0 10 10 2 26 0v10C16 12 12 18 12 24h14v26zM34 50V28C34 10 44 2 60 0v10C50 12 46 18 46 24h14v26z" fill="#b9d6de"/></svg>
    <div class="abs avatar" role="img" aria-label="Client portrait"></div>
    <div class="abs quote-text">Designing is a matter of concentration. You go deep into what you want to do. It's about intensive research,<br>really. The concentration is warm and<br>intimate and like</div>
    <div class="abs dots"><span></span><span class="on"></span><span></span></div>
    <svg class="abs" style="left:706px;top:256px" width="62" height="50" viewBox="0 0 62 50"><path d="M62 0v22c0 18-10 26-26 28V40c10-2 14-8 14-14H36V0zM28 0v22c0 18-10 26-26 28V40c10-2 14-8 14-14H2V0z" fill="#b9d6de"/></svg>
  </div>
</section>

<section class="blog">
  <div class="abs ghost" style="left:0;width:1200px;text-align:center;top:98px;font-size:58px">LATEST NEWS</div>
  <h2 class="abs title" style="left:0;width:1200px;text-align:center;top:132px">OUR BLOG</h2>

  <div class="abs post" style="left:98px">
    <div class="abs post-photo" role="img" aria-label="Two smiling clients beside a cabin"></div>
    <div class="abs post-title">Westbrook Clients</div>
    <div class="abs post-text">Lorem ipsum dolor sit amet, consectetur adipiscing elit, sed do eiusmod tempor incididunt ut labore et dolore magna aliqua.</div>
    <div class="abs post-meta"><span><svg width="13" height="13"><circle cx="6.5" cy="6.5" r="5.5" fill="none" stroke="#555" stroke-width="1.5"/><path d="M6.5 3.5v3h2.5" stroke="#555" fill="none"/></svg>Sep 10 '19</span><span><svg width="14" height="12"><path d="M1 1h12v7H6l-3 3V8H1z" fill="#333"/></svg>5 Comments</span></div>
  </div>
  <div class="abs post" style="left:440px">
    <div class="abs post-photo" role="img" aria-label="Young client standing by a cabin"></div>
    <div class="abs post-title">Lorem Ipsum is simply</div>
    <div class="abs post-text">Lorem ipsum dolor sit amet, consectetur adipiscing elit, sed do eiusmod tempor incididunt ut labore et dolore magna aliqua.</div>
    <div class="abs post-meta"><span><svg width="13" height="13"><circle cx="6.5" cy="6.5" r="5.5" fill="none" stroke="#555" stroke-width="1.5"/><path d="M6.5 3.5v3h2.5" stroke="#555" fill="none"/></svg>Sep 10 '19</span><span><svg width="14" height="12"><path d="M1 1h12v7H6l-3 3V8H1z" fill="#333"/></svg>5 Comments</span></div>
  </div>
  <div class="abs post" style="left:782px">
    <div class="abs post-photo" role="img" aria-label="Two clients holding gift cards in the studio"></div>
    <div class="abs post-title">Lakeside Clients</div>
    <div class="abs post-text">Lorem ipsum dolor sit amet, consectetur adipiscing elit, sed do eiusmod tempor incididunt ut labore et dolore magna aliqua.</div>
    <div class="abs post-meta"><span><svg width="13" height="13"><circle cx="6.5" cy="6.5" r="5.5" fill="none" stroke="#555" stroke-width="1.5"/><path d="M6.5 3.5v3h2.5" stroke="#555" fill="none"/></svg>Sep 10 '19</span><span><svg width="14" height="12"><path d="M1 1h12v7H6l-3 3V8H1z" fill="#333"/></svg>5 Comments</span></div>
  </div>
</section>

<footer class="footer">
  <svg class="abs" style="left:0;top:0" width="1200" height="40" viewBox="0 0 1200 40"><path d="M0 0H1200V14L1150 24 1100 12 1040 26 980 14 920 28 860 16 800 26 740 12 680 28 620 16 560 26 500 12 440 28 380 16 320 26 260 12 200 28 140 16 80 26 0 14Z" fill="#fff"/></svg>
  <div class="abs logo">Frost Haven</div>
  <div class="abs foot-about">Lorem ipsum dolor sit amet, consectetur adipiscing elit, sed do eiusmod tempor incididunt ut labore et dolore magna</div>

  <div class="abs foot-head" style="left:434px;top:88px">Contact Information</div>
  <div class="abs contact-line" style="left:436px;top:128px"><svg width="16" height="16" viewBox="0 0 16 16"><path d="M15 1 1 7l5 2 2 6z" fill="#222"/></svg><span>Suite 4, Harbor Lane, North Wing<br><span style="display:inline-block;margin-top:10px">88 Willow Street, floor 2</span></span></div>
  <div class="abs contact-line" style="left:436px;top:218px"><svg width="16" height="14" viewBox="0 0 16 14"><rect x="1" y="2" width="14" height="10" fill="#222"/><path d="M1 2l7 6 7-6" stroke="#a9cdd6" fill="none"/></svg><span>Email: hello@frosthaven.co</span></div>
  <div class="abs contact-line" style="left:436px;top:250px"><svg width="14" height="14" viewBox="0 0 24 24"><path d="M6.6 10.8a15 15 0 0 0 6.6 6.6l2.2-2.2c.3-.3.7-.4 1-.2 1.1.4 2.3.6 3.6.6.6 0 1 .4 1 1V20c0 .6-.4 1-1 1A17 17 0 0 1 3 4c0-.6.4-1 1-1h3.5c.6 0 1 .4 1 1 0 1.3.2 2.5.6 3.6.1.3 0 .7-.2 1z" fill="#222"/></svg><span>Phone: 555-014-2290</span></div>

  <div class="abs foot-head" style="left:774px;top:88px">Newsletter</div>
  <div class="abs" style="left:774px;top:128px;font-size:12.5px;color:#4d6f78">Enter your email &amp; subscribing newsletter</div>
  <div class="abs nl-input">Email address</div>
  <div class="abs nl-btn">SUBSCRIBE</div>
  <div class="abs ring" style="left:780px"></div>
  <div class="abs ring" style="left:812px"></div>
  <div class="abs ring" style="left:844px"></div>
  <div class="abs ring" style="left:876px"></div>

  <div class="abs foot-rule"></div>
  <div class="abs copyright">2019 © Copyrights. All rights reserved</div>
</footer>

</body>
</html>
```